Menu revision for Korean Restaurant

I have posted the exact content in a word file that I would like to appear in the menu. Please apply to the template. I will be following up with prices shortly. I am in a hurry and not too picky. Thank you.

Make a menu with revisions.

Page 1: Cover Page
- Replace logo with new uploaded logo

Page 2:
Appetizers
Vegetarian Appetizers

Page 3:
BBQ Items

Page 4:
Signature Dishes

Page 5:
Bokkeum | Stir-Fry

Page 6:
Rice Bowls
Noodles
Hot Soup

Page 7:
Drinks

My customers

Restaurant

• 1. Only use my menu content, template, and font.

```html
<!DOCTYPE html>
<html lang="en">
<head>
<meta charset="utf-8">
<title>Menu — Stir-Fry, Rice Bowls, Noodles, Hot Soup</title>
<link rel="stylesheet" href="https://fonts.googleapis.com/css2?family=Barlow+Semi+Condensed:wght@700&family=Barlow:wght@700&family=Libre+Baskerville&family=Noto+Serif+KR:wght@400&display=swap">
<style>
:root{
  --bg:#ffffff;
  --page:#1f2021;
  --gold:#b99a5b;
  --gold-line:#8d7544;
  --red:#c8262c;
  --text:#e7e3da;
}
*{margin:0;padding:0;box-sizing:border-box}
html,body{width:1200px;height:1200px;overflow:hidden;background:var(--bg)}
.canvas{position:relative;width:1200px;height:1200px}
.page{position:absolute;top:246px;width:553px;height:716px;background:var(--page);color:var(--text);
  font-family:"Libre Baskerville","Noto Serif KR",serif;font-size:8.9px;line-height:12px}
.page--left{left:33px}
.page--right{left:614px}
.frame{position:absolute;inset:0;width:553px;height:716px}
.section-title{position:absolute;left:0;width:100%;text-align:center;color:var(--red);
  font-family:"Barlow Semi Condensed",sans-serif;font-weight:700;font-size:34px;line-height:36px;letter-spacing:.5px}
.item{position:absolute;left:50px;width:460px;text-align:justify}
.page--right .item{left:46px;width:461px}
.dish,.label{color:var(--gold);font-family:"Barlow",sans-serif;font-weight:700;font-size:9px;letter-spacing:.5px}
.ko{color:var(--gold);font-family:"Noto Serif KR",serif;font-size:8.4px}
.photo{position:absolute;top:470px;width:222px;height:130px;border:1px solid var(--gold-line);
  background:radial-gradient(ellipse at 50% 45%,#c0461f 0%,#8a2a12 35%,#3a2a22 70%,#1a1512 100%)}
.photo-label{position:absolute;left:6px;top:6px;font-family:"Barlow",sans-serif;font-weight:700;font-size:6.8px;color:#fff;letter-spacing:.3px}
.photo-label .ko{color:#fff;font-size:6.2px}
.divider{position:absolute;height:1px;background:var(--gold-line)}
.seal{position:absolute;width:28px;height:28px;border-radius:50%;background:radial-gradient(circle,#6f5c36 0%,#4a3e27 60%,#2a251c 100%);border:1px solid var(--gold-line)}
.footnote{position:absolute;bottom:24px}
.page--left .footnote{left:50px}
.page--right .footnote{left:46px}
.col{position:absolute}
</style>
</head>
<body>
<div class="canvas">

  <section class="page page--left">
    <svg class="frame" viewBox="0 0 692 895" preserveAspectRatio="none" aria-hidden="true">
      <g fill="none" stroke="#8d7544" stroke-width="1.2">
        <path d="M11,46 H47 V13 H645 V46 H681 V849 H645 V882 H47 V849 H11 Z"/>
        <rect x="25" y="27" width="14" height="14"/><rect x="653" y="27" width="14" height="14"/>
        <rect x="25" y="854" width="14" height="14"/><rect x="653" y="854" width="14" height="14"/>
      </g>
    </svg>
    <h1 class="section-title" style="top:28px">BOKKEUM | STIR-FRY</h1>

    <p class="item" style="top:110px"><span class="dish">JEYUK BOKKEUM</span> <span class="ko">제육볶음</span> Pork, onions, scallions, mushrooms and jalapenos stir-fried in a spicy red garlic sauce.</p>
    <p class="item" style="top:159px"><span class="dish">DUBU BOKKEUM (V)</span> <span class="ko">두부볶음</span> Fried tofu cubes, zucchini, carrots, onions, and mushrooms stir-fried in a red chili sauce.</p>
    <p class="item" style="top:208px"><span class="dish">KIMCHI BOKKEUM</span> <span class="ko">김치볶음</span> Pork, kimchi, rice cakes, scallions, onions, and fresh tofu.</p>
    <p class="item" style="top:245px"><span class="dish">HAEMUL BOKKEUM</span> <span class="ko">해물볶음</span> Jumbo shrimp, scallops, mussels, calamari, octopus, zucchini, carrots, onions, scallions, mushrooms, and jalapenos.</p>
    <p class="item" style="top:294px"><span class="dish">SAMGYUPSAL BOKKEUM</span><span class="ko">매운삼겹살</span> Pork belly, zucchini, onions, scallions stir-fried in a spicy gochu wine sauce.</p>
    <p class="item" style="top:343px"><span class="dish">OJINGEO BOKKEUM</span> <span class="ko">오징어볶음</span> Fresh calamari stir-fried with carrots, zucchini, mushrooms, onions and scallions in a hot and spicy chili sauce.</p>
    <p class="item" style="top:392px"><span class="dish">NAKJI BOKKEUM</span> <span class="ko">낙지볶음</span> Fresh ctopus stir-fried with carrots, zucchini, mushrooms, onions, and scallions in a hot and spicy chili sauce.</p>
    <p class="item" style="top:440px"><span class="dish">JJUGGUMI SAMGYUPSAL</span> <span class="ko">쭈꾸미삼겹살</span> Spicy pork belly and baby octopus.</p>

    <div class="photo" style="left:48px" role="img" aria-label="Photo of glazed spicy chicken wings on a white plate">
      <span class="photo-label">SAMPLE TITLE <span class="ko">매운 닭날개</span></span>
    </div>
    <div class="photo" style="left:285px" role="img" aria-label="Photo of glazed spicy chicken wings on a white plate">
      <span class="photo-label">SAMPLE TITLE <span class="ko">매운 닭날개</span></span>
    </div>

    <div class="divider" style="left:161px;width:94px;top:638px"></div>
    <div class="seal" style="left:264px;top:624px" role="img" aria-label="Round seal ornament"></div>
    <div class="divider" style="left:300px;width:93px;top:638px"></div>

    <p class="footnote">* Menu items are subject to change without prior notice</p>
  </section>

  <section class="page page--right">
    <svg class="frame" viewBox="0 0 692 895" preserveAspectRatio="none" aria-hidden="true">
      <g fill="none" stroke="#8d7544" stroke-width="1.2">
        <path d="M11,46 H47 V13 H645 V46 H681 V849 H645 V882 H47 V849 H11 Z"/>
        <rect x="25" y="27" width="14" height="14"/><rect x="653" y="27" width="14" height="14"/>
        <rect x="25" y="854" width="14" height="14"/><rect x="653" y="854" width="14" height="14"/>
      </g>
    </svg>
    <h2 class="section-title" style="top:28px">RICE BOWLS</h2>

    <p class="item" style="top:79px"><span class="dish">*YUKHWE BIBIMBAP</span> <span class="ko">육회비빔밥</span> Raw beef tartar &amp; egg yolk on rice with a colorful spread of spinach, carrots, bean sprouts, soybean sprouts, shiitake mushrooms, zucchini, and radish. Topped with garlic and pine nuts &amp; served with a side of house-made gochujang &amp; bowl of rice.</p>
    <p class="item" style="top:126px"><span class="dish">*DOLSOT BIBIMBAP</span> <span class="ko">돌솥비빔밥</span> Sizzling hot stone bowl bibimbap. Individually marinated spinach, carrots, bean sprouts, soybean sprouts, shiitake mushrooms, zucchini, and radish topped with choice of fried egg or raw egg. Served with a side of house-made gochujang sauce.</p>

    <div class="col" style="left:46px;top:173px">
      <div class="label">DIRECTIONS:</div>
      <div>1. Add gochujang</div>
      <div>2. Mix</div>
    </div>
    <div class="col" style="left:209px;top:173px">
      <div class="label">CHOOSE CENTERPIECE:</div>
      <div>Tofu or Kimchi:</div>
      <div>Bulgogi (original) or Chicken:</div>
      <div>Kimchi &amp; Pork:</div>
      <div>Seafood:</div>
    </div>

    <div class="divider" style="left:158px;width:95px;top:264px"></div>
    <div class="seal" style="left:262px;top:250px" role="img" aria-label="Round seal ornament"></div>
    <div class="divider" style="left:299px;width:91px;top:264px"></div>

    <h2 class="section-title" style="top:296px">NOODLE DISHES</h2>
    <p class="item" style="top:343px"><span class="dish">MUL NAENG MYUN</span> <span class="ko">물냉면</span>Beef brisket, pickled radish, cucumbers slices, jalapenos, and hard-boiled egg layered on top of thin buckwheat noodles in icy beef broth.</p>
    <p class="item" style="top:378px"><span class="dish">BIBIM NAENG MYUN</span> <span class="ko">비빔냉면</span>Pickled radish, cucumber slices, jalapenos, scallions, and hard-boiled egg set atop a mound of sweet &amp; spicy buckwheat noodles.</p>

    <h2 class="section-title" style="top:474px">HOT SOUP</h2>
    <p class="item" style="top:517px"><span class="dish">*SOON DUBU CHIGAE</span> <span class="ko">순두부찌개</span> Soft tofu stew with mushrooms, egg, and choice of protein in boiling spicy chili oil broth.</p>
    <div class="col" style="left:46px;top:553px">Vegetarian</div>
    <div class="col" style="left:150px;top:553px">Beef, Chicken, or Pork</div>
    <div class="col" style="left:307px;top:553px">Seafood</div>
    <p class="item" style="top:576px"><span class="dish">KIMCHI CHIGAE</span> <span class="ko">김치찌개</span> Kimchi, pork, tofu, fish cake, scallions, mushrooms and spicy pepper flakes in boiling kimchi broth.</p>
    <p class="item" style="top:611px"><span class="dish">GALBI TANG</span> <span class="ko">갈비탕</span> Beef short rib soup with radishes, mushrooms, scallions, vermicelli noodles.</p>

    <p class="footnote">* Menu items are subject to change without prior notice</p>
  </section>

</div>
</body>
</html>
```